Verodex business card

Business card for sustainable investment company called "Verodex". Verodex is an exchange platform selling carbon credits between buyers and sellers. Carbon Credits are an environmental commodity for reducing global carbon emissions.

the card should obviously have our logo and the theme should be sustainability/environment mixed with a trading platform.

Contact Information for Business Card

Logo, Name, Title, Phone, Email

Colors
0054AA
0677BA
7BADD7
CADEEF
E8F1F8
0094D4
00A9DD
6FCCEA
C7EBF8
E9F6FB
00AB8E
00BBA5
67D7C9
C6EFE9
E9F9F6
59FF00
82FF00
B8FF75
E3FFCB
F4FFEA

```html
<!DOCTYPE html>
<html lang="en">
<head>
<meta charset="utf-8">
<title>Verodex business card</title>
<link rel="stylesheet" href="https://fonts.googleapis.com/css2?family=Open+Sans:ital,wght@0,400;0,600;0,700;0,800&display=swap">
<style>
  :root {
    --page: #e9ecef;
    --card-dark: #202125;
    --card-pattern: #26272b;
    --blue-light: #5fc6dc;
    --blue-mid: #4e9fd0;
    --blue-deep: #4a6fc0;
    --white: #ffffff;
    --text-soft: #e8e8ea;
  }
  * { margin: 0; padding: 0; box-sizing: border-box; }
  html, body {
    width: 1200px;
    height: 780px;
    overflow: hidden;
    background: var(--page);
    font-family: "Open Sans", Arial, sans-serif;
  }
  .canvas {
    width: 1200px;
    height: 780px;
    display: flex;
    align-items: center;
    justify-content: center;
    gap: 44px;
  }
  .card {
    position: relative;
    width: 540px;
    height: 310px;
    border-radius: 22px;
    overflow: hidden;
    background: var(--card-dark);
    box-shadow: 0 10px 28px rgba(0,0,0,0.18);
  }
  .card-wave {
    position: absolute;
    inset: 0;
    width: 100%;
    height: 100%;
  }
  .brand {
    position: absolute;
    top: 30px;
    left: 34px;
    display: flex;
    align-items: center;
    gap: 12px;
  }
  .brand-square {
    width: 24px;
    height: 24px;
    background: var(--blue-mid);
  }
  .brand-name {
    color: var(--white);
    font-weight: 700;
    font-size: 30px;
    letter-spacing: 0.5px;
    line-height: 1;
  }
  .contact {
    position: absolute;
    top: 82px;
    left: 34px;
    color: var(--text-soft);
    font-size: 12.5px;
    line-height: 1.45;
  }
  .contact-address { margin-bottom: 4px; }
  .contact-line {
    display: flex;
    align-items: center;
    gap: 7px;
  }
  .contact-icon { width: 11px; height: 11px; flex: none; }
  .person {
    position: absolute;
    right: 40px;
    top: 142px;
    text-align: right;
  }
  .person-name {
    font-size: 27px;
    font-weight: 800;
    line-height: 1.1;
    letter-spacing: 0.6px;
  }
  .person-first { color: var(--blue-mid); }
  .person-last { color: var(--white); }
  .person-title {
    color: var(--white);
    font-size: 15px;
    font-weight: 600;
    letter-spacing: 1px;
    margin-top: 4px;
  }
  .title-tab {
    position: absolute;
    right: 0;
    top: 146px;
    width: 22px;
    height: 54px;
    background: linear-gradient(180deg, var(--blue-light), var(--blue-mid));
  }
  .card-back { background: var(--card-dark); }
  .back-pattern {
    position: absolute;
    inset: 0;
    background: var(--card-pattern);
  }
  .back-brand {
    position: absolute;
    left: 318px;
    top: 196px;
    color: var(--blue-mid);
    font-weight: 700;
    font-size: 18px;
    letter-spacing: 0.5px;
  }
</style>
</head>
<body>
<main class="canvas">
  <section class="card card-front" aria-label="Card front">
    <svg class="card-wave" viewBox="0 0 540 310" aria-hidden="true">
      <defs>
        <linearGradient id="waveBlue" x1="0" y1="0" x2="1" y2="1">
          <stop offset="0" stop-color="#5fc6dc"/>
          <stop offset="0.55" stop-color="#4e9fd0"/>
          <stop offset="1" stop-color="#4a6fc0"/>
        </linearGradient>
      </defs>
      <path d="M0,175 C60,225 150,250 270,262 C340,268 390,280 430,310 L0,310 Z" fill="url(#waveBlue)"/>
      <path d="M0,168 C40,205 85,228 140,244" fill="none" stroke="#ffffff" stroke-width="4" stroke-linecap="round"/>
    </svg>

    <div class="brand">
      <span class="brand-square"></span>
      <span class="brand-name">VERODEX</span>
    </div>

    <div class="contact">
      <p class="contact-address">4180 Linden Ave. Suite 310<br>Harlow, TX 75400</p>
      <p class="contact-line">
        <svg class="contact-icon" viewBox="0 0 12 12"><path d="M3 1 L5 3.5 L4 5 C4.6 6.4 5.6 7.4 7 8 L8.5 7 L11 9 L9.6 11 C5 10.6 1.4 7 1 2.4 Z" fill="#fff"/></svg>
        (555) 014-2298
      </p>
      <p class="contact-line">
        <svg class="contact-icon" viewBox="0 0 12 12"><rect x="1" y="2.5" width="10" height="7" fill="#fff"/><path d="M1 2.5 L6 6.5 L11 2.5" fill="none" stroke="#202125" stroke-width="1"/></svg>
        info@verodex.com
      </p>
      <p class="contact-line">
        <svg class="contact-icon" viewBox="0 0 12 12"><circle cx="6" cy="6" r="5" fill="#fff"/><path d="M1 6 H11 M6 1 C3.5 4 3.5 8 6 11 M6 1 C8.5 4 8.5 8 6 11" fill="none" stroke="#202125" stroke-width="0.8"/></svg>
        www.verodex.com
      </p>
    </div>

    <div class="person">
      <p class="person-name"><span class="person-first">Mara</span> <span class="person-last">Delvin</span></p>
      <p class="person-title">Co-Founder</p>
    </div>
    <span class="title-tab"></span>
  </section>

  <section class="card card-back" aria-label="Card back">
    <div class="back-pattern" role="img" aria-label="Repeating tone-on-tone brand pattern across the card back"></div>
    <span class="back-brand">VERODEX</span>
  </section>
</main>
</body>
</html>
```